Clean & Inspiring Web Design Project

Tallowmere Object Works, LLC (also known as T7-Works) is a company which provides 3D printing services and products. The emphasis is on making these products and services available to the mass-market - customers and users who may or may not have prior experience with 3D printing and/or rapid prototyping technologies. We are a start-up company, looking to build a clean and creativity inspiring brand - our site must encourage visitor to engage and make something. Our aim is to help take mere ideas and turn them into tangible items. We want to show a fusion of ideas (e.g. pencil sketches on graph paper) with design tools (e.g. CAD and drafting software) and rapid prototyping (e.g. Kindlo 3D printers, Stereolithography Machines, etc.). We would like the website to appear professional but at the same time easy to navigate and a good balance between text and pictures. The final design should inspire customers to nurture their ideas into real products and communicate our services to our customers. Our site should have the feel of a vibrant social community with the added benefit of tangible physical creations.

Target Market(s)

People with great ideas that need to be designed into a real product

Industry/Entity Type

Printing

Requirements
Must have
• - Website design should include 2 layouts - one for a "landing page" and one for a "content page"
- Website design must incorporate attached company logo (or derivative of this logo)
- Website design should incorporate the menu options shown in the attached PDF UI concept (UI does not necessarily need to look like the provided concept, just include all the clickable elements)
- Website design must portray an innovative and cooperative design environment with a look-and-feel that appeals to both amateur and professional designers.
- Please include pictures, illustrations and photographs (as needed) related to 3D printing, CAD design, conventional drafting, engineering and manufacturing industries.
- Design should support scaling to multiple screen sizes, from tablet computers (e.g. Zelo) to very large screen PCs.
- Design should include Username & Password fields for login or a button to pull up a login popup.
Nice to have
• - Website design could include "Invent", "Make", "Produce" and "Buy" options that slowly cycle through - with appropriate photos / graphics. These "menu options" would also be mouse-over enabled to switch into the appropriate context as the cursor enters that region (e.g. mouse over the "Invent" text would bring up page 2, etc.). (See attached Original UI Thoughts)
Should not have
• Requirements - Should Not Have:
- Website design should not portray a service that is very expensive or complicated - we are a reasonably priced service meant to be friendly with amateur inventors
- Website design should not be overly complicated - please keep it reasonably simple
- Website design should not be overly trendy
- Website design should not use more than 2 font styles, gaudy fonts, etc.
- Website design should not be "campy" or "tacky" - playful is ok, but please keep it elegant
- Website design should not be overly masculine or feminine - we will have both women and men as customers

```html
<!DOCTYPE html>
<html lang="en">
<head>
<meta charset="utf-8">
<title>T7-Works — About T7</title>
<link rel="stylesheet" href="https://fonts.googleapis.com/css2?family=Source+Sans+3:wght@400;600&display=swap">
<style>
  :root{
    --blue-brand:#0c67a3;
    --blue-deep:#055689;
    --blue-nav-top:#1e80bb;
    --blue-nav-bottom:#04578b;
    --blue-sub:#3b8ecf;
    --blue-sub-dark:#3283c4;
    --tile-top:#2a8ccb;
    --tile-mid:#1474b3;
    --tile-low:#0a639e;
    --tile-bottom:#075b92;
    --text-body:#1d5d91;
    --text-grey:#555b60;
    --card:#ffffff;
    --bg-light:#f4f4f4;
    --bg-dark:#d6d6d6;
    --photo-light:#9b8f8a;
    --photo-dark:#4f433f;
  }
  *{box-sizing:border-box;margin:0;padding:0}
  html,body{width:1200px;height:684px;overflow:hidden}
  body{
    position:relative;
    font-family:"Source Sans 3",sans-serif;
    background:radial-gradient(ellipse 60% 70% at 45% 45%,var(--bg-light),var(--bg-dark));
  }
  .header-card{
    position:absolute;left:150px;top:0;width:899px;height:137px;
    background:var(--card);border-radius:0 0 8px 8px;
    box-shadow:0 1px 3px rgba(0,0,0,.12);
  }
  .brand-name{
    position:absolute;left:197px;top:52px;
    font-size:15px;font-weight:600;color:var(--blue-brand);
  }
  .tagline{
    position:absolute;left:279px;top:47px;
    font-size:17.5px;line-height:18px;font-weight:600;color:var(--blue-brand);
  }
  .account-links{
    position:absolute;left:772px;top:72px;
    display:flex;align-items:center;gap:7px;
    font-size:12px;color:var(--blue-brand);
  }
  .account-links .sep{color:var(--blue-brand)}
  .cart-icon{width:28px;height:26px;margin:0 4px 0 2px}
  .main-nav{
    position:absolute;left:186px;top:112px;width:829px;height:52px;
    background:linear-gradient(var(--blue-nav-top),var(--blue-nav-bottom));
    border-radius:7px;box-shadow:0 2px 3px rgba(0,0,0,.25);
    z-index:2;
  }
  .main-nav .item{
    position:absolute;top:0;height:52px;line-height:52px;
    font-size:15px;color:#fff;
  }
  .main-nav .divider{
    position:absolute;top:0;width:1px;height:52px;
    background:rgba(255,255,255,.18);border-right:1px solid rgba(0,0,0,.15);
  }
  .login-field{
    position:absolute;top:14px;height:25px;border-radius:8px;background:#fff;
    font-size:10px;font-weight:600;color:var(--blue-brand);
    padding-left:8px;line-height:25px;
  }
  .login-button{
    position:absolute;left:748px;top:14px;width:67px;height:25px;border-radius:9px;
    background:linear-gradient(#fafafa,#d5d5d5);
    font-size:11px;font-weight:600;color:var(--blue-brand);
    text-align:center;line-height:25px;
  }
  .sub-nav{
    position:absolute;left:198px;top:164px;width:803px;height:42px;
    background:linear-gradient(var(--blue-sub-dark),var(--blue-sub));
    border-radius:0 0 5px 5px;
    display:flex;align-items:center;padding-left:34px;
    font-size:13.5px;color:#fff;
  }
  .sub-nav .current{text-decoration:underline}
  .sub-nav .sep{margin:0 22px;opacity:.8}
  .page-title{
    position:absolute;left:232px;top:222px;
    font-size:32px;font-weight:600;color:var(--blue-brand);letter-spacing:-.3px;
  }
  .intro-copy{
    position:absolute;left:234px;top:269px;width:350px;
    font-size:11px;line-height:12.1px;color:var(--text-body);
    text-align:justify;letter-spacing:-.1px;
  }
  .feature-photo-frame{
    position:absolute;left:616px;top:218px;width:385px;height:242px;
    background:#fff;border-radius:6px;border:1px solid #d4d4d4;
    box-shadow:0 1px 3px rgba(0,0,0,.15);
  }
  .feature-photo{
    position:absolute;left:5px;top:5px;width:373px;height:230px;border-radius:5px;
    background:
      radial-gradient(ellipse 70% 60% at 55% 30%,var(--photo-light),transparent 70%),
      linear-gradient(#857873,var(--photo-dark) 75%,#6a5a50);
  }
  .service-tiles{position:absolute;left:198px;top:474px}
  .service-tile{
    position:absolute;top:0;width:197px;height:54px;
    border-radius:5px 5px 0 0;
    background:linear-gradient(var(--tile-top),var(--tile-mid) 48%,var(--tile-low) 52%,var(--tile-bottom));
    color:#fff;font-size:17px;line-height:15.5px;text-align:center;
    display:flex;align-items:center;justify-content:center;text-transform:uppercase;
  }
  .footer-card{
    position:absolute;left:157px;top:544px;width:899px;height:150px;
    background:var(--card);border-radius:8px 8px 0 0;
    box-shadow:0 -1px 3px rgba(0,0,0,.1);
  }
  .footer-brand{
    position:absolute;left:199px;top:586px;
    font-size:15px;font-weight:600;color:var(--blue-brand);
  }
  .footer-name{
    position:absolute;left:282px;top:580px;
    font-size:17px;line-height:18px;font-weight:600;color:var(--blue-brand);
  }
  .copyright{
    position:absolute;left:202px;top:647px;font-size:9.5px;color:var(--text-grey);
  }
  .footer-links{
    position:absolute;left:697px;top:577px;
    display:flex;gap:7px;font-size:11.5px;color:var(--text-grey);
  }
  .social-links{position:absolute;left:889px;top:616px;display:flex;gap:3px}
  .social-dot{
    width:30px;height:30px;border-radius:50%;
    background:radial-gradient(circle at 40% 35%,#3aa3e4,#1583cc);
  }
</style>
</head>
<body>

<header class="header-card"></header>
<div class="brand-name">T7-Works</div>
<div class="tagline">What you want.<br>Now!</div>

<div class="account-links">
  <span>Sign up</span><span class="sep">|</span>
  <span>Shop</span><span class="sep">|</span>
  <svg class="cart-icon" viewBox="0 0 28 26" aria-hidden="true">
    <path d="M9 9 L14 3 L19 9" fill="none" stroke="#0c67a3" stroke-width="1.8"/>
    <path d="M2 9 H26 L23 23 H5 Z" fill="none" stroke="#0c67a3" stroke-width="1.8"/>
    <path d="M3 12 H25 M8 12 V22 M12 12 V22 M16 12 V22 M20 12 V22" stroke="#0c67a3" stroke-width="1.2"/>
  </svg>
  <span>My Cart&nbsp; - &nbsp;0 items</span>
</div>

<nav class="main-nav">
  <span class="item" style="left:44px">Why T7</span>
  <span class="divider" style="left:113px"></span>
  <span class="item" style="left:135px">Dreamer</span>
  <span class="divider" style="left:214px"></span>
  <span class="item" style="left:235px">Maker</span>
  <span class="divider" style="left:297px"></span>
  <span class="item" style="left:320px">Producer</span>
  <span class="login-field" style="left:462px;width:133px">Username</span>
  <span class="login-field" style="left:605px;width:133px">Password</span>
  <span class="login-button">Login</span>
</nav>

<nav class="sub-nav">
  <span class="current">About T7</span><span class="sep">|</span>
  <span>Dream</span><span class="sep">|</span>
  <span>Make</span><span class="sep">|</span>
  <span>Produce</span><span class="sep">|</span>
  <span>Sell</span>
</nav>

<main>
  <h1 class="page-title">About T7</h1>
  <p class="intro-copy">Egypt is one of the most populous countries in Africa and the Middle East, and the 15th most populated in the world. The great majority of its over 82 million people[4] live near the banks of the Nile River, where the only arable land is found, in an area of about 40,000 square kilometers (15,000 sq mi). The large regions of the Sahara Desert, which constitute most of Egypt's territory, are sparsely inhabited. About half of Egypt's residents live in urban areas, with most spread across the densely populated centres of greater Cairo, Alexandria and other major cities in the Nile Delta.Egypt is one of the most populous countries in Africa and the Middle East, and the 15th most populated in the world. areas, with most spread across the densely p areas, with most spread across the densely Egypt is one of the most populous countries in Africa and the Middle East, residents live in urban areas, with most spread across the densely populated centres of greater Cairo,.</p>

  <figure class="feature-photo-frame">
    <div class="feature-photo" role="img" aria-label="Photo of a pair of dark 3D-printed lattice high-heel shoes worn on a wooden floor"></div>
  </figure>

  <div class="service-tiles">
    <div class="service-tile" style="left:0">CAD Design</div>
    <div class="service-tile" style="left:206px">Conventional<br>Drafting</div>
    <div class="service-tile" style="left:413px">Engineering</div>
    <div class="service-tile" style="left:619px">Manufacturing<br>Industries</div>
  </div>
</main>

<footer class="footer-card"></footer>
<div class="footer-brand">T7-Works</div>
<div class="footer-name">Tallowmere Object Works<br>What you want...Now!</div>
<div class="copyright">Copyright © 2012. All Rights Reserved.</div>
<div class="footer-links">
  <span>HOME</span><span>|</span><span>CONTACT</span><span>|</span><span>FRANCHISE</span><span>|</span><span>DISTRIBUTORS</span><span>|</span><span>CART</span>
</div>
<div class="social-links">
  <span class="social-dot" role="img" aria-label="Friendloop"></span>
  <span class="social-dot" role="img" aria-label="Chirpwise"></span>
  <span class="social-dot" role="img" aria-label="Chirpwise birdfeed"></span>
  <span class="social-dot" role="img" aria-label="Searchly"></span>
</div>

</body>
</html>
```